Web and Logo Design for eCommerce site

We're launching a sister brand and require a full design for the site.

The site must have an established feel and appeal to corporate and institutional buyers.
Updates

Just a note about the wireframe design:

The Search & Rescue / Coast Guard / NVDK, etc. in the header area aren't buttons or menu items, but rather just info (along the lines of a tagline).  Sort of a "who we serve" sort of thing.

Worth noting is that it's specifically geared towards LARGE BUYERS.  For example, a police force buying 200 headlamps and 85 pairs of gloves.  So they'll register + sign in and then add a bunch of items to a RFQ.

Aim for a professional, masculine design.

Target Market(s)

We will be selling outdoor gear to the military, law enforcement, fire and rescue and first responders.

Requirements
Must have
• We require:
- Logo (vector based)

Site:
- template page
* main site template, re-skinned version of our current site
* horizontal drop-down menu
- product listings page
* thumbnail view of products
- product details page
* including elements such as product image, color/size selector, descriptions and specs (again, based loosely on our current website)
- account management page
* illustrating basic data entry styles for text box, buttons, grid, etc.

The site needs to be given a responsive design, so 2 versions of each design should be presented for desktop + mobile views.

Additional funds are available if the designer is able to fully implement the designs into a responsive framework such as bootstrap.

Nice to have
• Clean, professional design similar to:

http://military.trailvexagear.com/gov/accessories/gloves.html

http://leaf.ombrivo.com/ProductFind.aspx?language=EN&category=Hardshell&subcat=Waterproof_Jackets

```html
<!DOCTYPE html>
<html lang="en">
<head>
<meta charset="utf-8">
<title>Norvane – Northern Field Gear Supply</title>
<link href="https://fonts.googleapis.com/css2?family=Arimo:wght@400;700&display=swap" rel="stylesheet">
<style>
:root{
  --dark:#3d3d3d;
  --darker:#333;
  --blue:#3a97d8;
  --blue-dark:#2a82c2;
  --light:#f3f3f3;
  --line:#dcdcdc;
  --text:#444;
  --muted:#888;
  --white:#fff;
}
*{box-sizing:border-box;margin:0;padding:0}
html,body{width:838px;height:1200px;overflow:hidden;background:var(--white);font-family:"Arimo",Arial,sans-serif;color:var(--text)}
.page{position:relative;width:838px;height:1200px}
.abs{position:absolute}

/* top header */
.topbar{left:0;top:0;width:838px;height:63px;background:var(--dark)}
.brand{left:90px;top:10px;color:var(--blue);font-size:27px;line-height:28px}
.brand small{display:block;color:#ddd;font-size:8px;line-height:12px;margin-top:1px}
.login{left:372px;top:22px;height:20px;display:flex;align-items:center;border:1px solid #555;font-size:9px;color:#eee}
.login .lock{width:20px;height:20px;background:var(--blue);display:flex;align-items:center;justify-content:center}
.login span{padding:0 6px}
.tagline{right:92px;top:16px;text-align:right;color:#eee;font-size:11px;line-height:16px}

/* who we serve */
.serve{left:0;top:63px;width:838px;height:37px;background:linear-gradient(#fff,#ececec);border-bottom:1px solid var(--line)}
.serve ul{list-style:none;display:flex;position:absolute;left:92px;top:0;height:37px;align-items:center;font-size:10.5px;color:#555}
.serve li{padding:0 14px;border-right:1px solid #ccc;line-height:14px}
.serve li:last-child{border-right:0}
.search{left:623px;top:70px;width:124px;height:23px;border:1px solid var(--blue);display:flex;background:#fff}
.search .field{flex:1;display:flex;align-items:center;padding-left:5px}
.search button{width:44px;border:0;background:var(--blue);color:#fff;font:9px "Arimo",sans-serif}

/* main menu */
.menu{left:0;top:100px;width:838px;height:37px;background:var(--blue)}
.menu ul{list-style:none;display:flex;justify-content:space-between;position:absolute;left:92px;right:92px;top:0;height:37px;align-items:center;color:#fff;font-size:10.5px}

/* hero */
.hero{left:0;top:137px;width:838px;height:313px;background:linear-gradient(135deg,#f4f6f8 0%,#cfd6dc 35%,#8c959c 55%,#e8ecef 80%,#dfe4e8 100%)}
.dots{left:388px;top:402px;display:flex;gap:5px}
.dots i{width:11px;height:11px;border-radius:50%;border:2px solid #fff;display:block}
.dots i.on{border-color:var(--blue);background:#fff}

/* sidebar */
.cats{left:92px;top:472px;width:154px;border:1px solid var(--line);background:#fff}
.cats h3{background:var(--blue);color:#fff;font-weight:400;font-size:12px;height:21px;display:flex;align-items:center;justify-content:space-between;padding:0 7px;margin:1px}
.cats ul{list-style:none;padding:0 11px 3px 8px}
.cats li{font-size:7.5px;color:#555;height:23px;display:flex;align-items:center;justify-content:space-between;border-bottom:1px solid #e6e6e6}
.cats li:last-child{border-bottom:0}
.promo{left:92px;top:725px;width:154px;height:115px;background:linear-gradient(160deg,#4a4a48,#2d2a26 60%,#6a5a48)}

/* products */
.feat-head{left:266px;top:470px;width:480px;height:24px;border:1px solid var(--line);background:linear-gradient(#fafafa,#eee);display:flex;align-items:center;justify-content:space-between;padding:0 8px}
.feat-head h2{font-weight:400;font-size:12px;color:#333}
.sort{font-size:9px;color:var(--muted)}
.sort b{font-weight:400;color:#333}
.sort em{font-style:normal;color:var(--blue)}
.card{width:151px;height:157px;border:1px solid var(--line);background:#fff;overflow:hidden}
.card .thumb{position:relative;height:108px;display:flex;align-items:center;justify-content:center}
.card .ph{width:46px;height:66px;border-radius:6px}
.card .badge{position:absolute;left:0;top:0}
.card .info{background:#f3f3f3;height:49px;text-align:center;padding-top:11px}
.card .name{font-size:8.5px;color:#333}
.card .price{font-size:9.5px;color:var(--blue);margin-top:4px}
.pager{left:415px;top:862px;display:flex;gap:3px}
.pager i{font-style:normal;width:13px;height:13px;border:1px solid #bbb;border-radius:50%;font-size:6.5px;display:flex;align-items:center;justify-content:center;color:#333;background:#fafafa}
.pager i.on{background:var(--blue);border-color:var(--blue);color:#fff}

/* testimonials */
.testi{left:0;top:898px;width:838px;height:46px;background:var(--blue)}
.testi .tag{position:absolute;left:87px;top:11px;height:24px;width:84px;background:var(--blue-dark);color:#fff;font-size:9.5px;display:flex;align-items:center;padding-left:10px}
.testi .tag:after{content:"";position:absolute;right:-12px;top:0;border-left:12px solid var(--blue-dark);border-top:12px solid transparent;border-bottom:12px solid transparent}
.testi p{position:absolute;left:210px;top:12px;width:440px;color:#fff;font-size:8.5px;line-height:12px}
.testi .next{position:absolute;left:705px;top:7px;width:40px;height:31px;background:var(--blue-dark);display:flex;align-items:center;justify-content:center}

/* footer */
.footer{left:0;top:944px;width:838px;height:194px;background:var(--dark);color:#eee}
.col{position:absolute;top:26px}
.col h4{font-weight:400;font-size:14px;margin-bottom:10px}
.col ul{list-style:none;font-size:7.8px;line-height:16.4px}
.col li:before{content:"›";font-weight:700;font-size:11px;margin-right:7px}
.col p{font-size:7.5px;line-height:15px;width:136px}
.col .input{width:134px;height:18px;background:#eee;border:1px solid #ccc;color:#999;font-size:7px;padding:4px;margin-top:10px}
.col .input+.input{margin-top:12px}
.col .sub{display:inline-block;background:var(--blue);color:#fff;font-size:10px;padding:3px 5px;margin-top:12px}
.bottom{left:0;top:1138px;width:838px;height:62px;background:var(--darker)}
.copy{left:95px;top:1165px;font-size:7.5px;color:#ccc}
.social{left:616px;top:1156px;display:flex;gap:6px}
.social i{width:28px;height:28px;border-radius:50%;background:#c4c4c4;display:block}
</style>
</head>
<body>
<div class="page">

  <header class="abs topbar"></header>
  <div class="abs brand">Norvane<small>Northern Field Gear Supply</small></div>
  <div class="abs login">
    <div class="lock"><svg width="9" height="11" viewBox="0 0 9 11"><path d="M2 5V3.5a2.5 2.5 0 0 1 5 0V5" fill="none" stroke="#fff" stroke-width="1.3"/><rect x="0.5" y="5" width="8" height="6" rx="1" fill="#fff"/></svg></div>
    <span>Customer Login</span>
  </div>
  <div class="abs tagline">“ Great Outdoor Gear For<br>Canada’s First Responders”</div>

  <nav class="abs serve">
    <ul><li>Search &amp; Rescue</li><li>Coast Guard</li><li>NVDK</li><li>Fire</li><li>Military</li><li>Law Enforcement</li></ul>
  </nav>
  <div class="abs search">
    <div class="field"><svg width="12" height="12" viewBox="0 0 12 12"><circle cx="5" cy="5" r="3.6" fill="none" stroke="#999" stroke-width="1.3"/><path d="M7.7 7.7L11 11" stroke="#999" stroke-width="1.5"/></svg></div>
    <button>Search</button>
  </div>

  <nav class="abs menu">
    <ul><li>Resucue Gear</li><li>Footwear</li><li>Clothing</li><li>Tents, Mats, Sleeping Bags</li><li>Camping Gear</li><li>Snow Sports</li><li>Brands</li></ul>
  </nav>

  <section class="abs hero" role="img" aria-label="Climber in an orange jacket ascending a snowy mountain ridge"></section>
  <div class="abs dots"><i class="on"></i><i></i><i></i><i></i></div>

  <aside class="abs cats">
    <h3>Categories <svg width="13" height="13" viewBox="0 0 13 13"><circle cx="6.5" cy="6.5" r="5.6" fill="none" stroke="#fff" stroke-width="1.1"/><path d="M4 5.5l2.5 2.5L9 5.5" fill="none" stroke="#fff" stroke-width="1.2"/></svg></h3>
    <ul>
      <li>Quisque semper justo at risus<span>›</span></li>
      <li>Amet lectus quis est congue<span>›</span></li>
      <li>Proin nibh augue</li>
      <li>Quisque semper justo at risus<span>›</span></li>
      <li>Amet lectus quis est congue</li>
      <li>Proin nibh augue<span>›</span></li>
      <li>Etiam sit amet lectus quis<span>›</span></li>
      <li>Proin nibh augue</li>
      <li>Etiam sit amet lectus quis</li>
    </ul>
  </aside>
  <div class="abs promo" role="img" aria-label="Member adventure pass promotion banner"></div>

  <div class="abs feat-head">
    <h2>Featured Products</h2>
    <div class="sort">Sort By: <b>Defult</b><em>▾</em> &nbsp;/&nbsp; Price &nbsp;/&nbsp; Name</div>
  </div>

  <div class="abs card" style="left:267px;top:509px"><div class="thumb"><svg class="badge" width="26" height="26"><path d="M0 0h26L0 26z" fill="#3a97d8"/></svg><div class="ph" role="img" aria-label="Red hardshell jacket" style="background:#e8402a"></div></div><div class="info"><div class="name">Etiam sit amet lectus quis</div><div class="price">$780.00</div></div></div>
  <div class="abs card" style="left:431px;top:509px"><div class="thumb"><svg class="badge" width="26" height="26"><path d="M0 0h26L0 26z" fill="#3a97d8"/></svg><div class="ph" role="img" aria-label="Blue and white ski boot" style="background:linear-gradient(#4bb0d8,#d8e4ea)"></div></div><div class="info"><div class="name">Etiam sit amet lectus quis</div><div class="price">$780.00</div></div></div>
  <div class="abs card" style="left:595px;top:509px"><div class="thumb"><svg class="badge" width="26" height="26"><path d="M0 0h26L0 26z" fill="#3a97d8"/></svg><div class="ph" role="img" aria-label="Avalanche beacon" style="width:22px;height:44px;background:#7a8a80"></div></div><div class="info"><div class="name">Etiam sit amet lectus quis</div><div class="price">$780.00</div></div></div>
  <div class="abs card" style="left:267px;top:681px"><div class="thumb"><svg class="badge" width="26" height="26"><path d="M0 0h26L0 26z" fill="#3a97d8"/></svg><div class="ph" role="img" aria-label="Orange avalanche shovel" style="width:34px;background:#d9703a"></div></div><div class="info"><div class="name">Etiam sit amet lectus quis</div><div class="price">$780.00</div></div></div>
  <div class="abs card" style="left:431px;top:681px"><div class="thumb"><svg class="badge" width="26" height="26"><path d="M0 0h26L0 26z" fill="#3a97d8"/></svg><div class="ph" role="img" aria-label="Blue and white ski boot" style="background:linear-gradient(#4bb0d8,#d8e4ea)"></div></div><div class="info"><div class="name">Etiam sit amet lectus quis</div><div class="price">$780.00</div></div></div>
  <div class="abs card" style="left:595px;top:681px"><div class="thumb"><svg class="badge" width="26" height="26"><path d="M0 0h26L0 26z" fill="#3a97d8"/></svg><div class="ph" role="img" aria-label="Pair of patterned skis" style="width:26px;background:linear-gradient(90deg,#2c6e74,#c95a2e,#2c6e74)"></div></div><div class="info"><div class="name">Etiam sit amet lectus quis</div><div class="price">$780.00</div></div></div>

  <div class="abs pager"><i>«</i><i>1</i><i class="on">2</i><i>3</i><i>4</i><i>5</i><i>6</i><i>7</i><i>8</i><i>9</i><i>10</i><i>»</i></div>

  <section class="abs testi">
    <div class="tag">Testimonials</div>
    <p>Lorem ipsum dolor sit amet, consectetur adipiscing elit. Praesent libero lectus, tempus sed aliquam non, pellentesque et eros. Donec luctus nisl in nibh ultricies quis convallis justo convallis. R.K Dalton, BC</p>
    <div class="next"><svg width="18" height="16" viewBox="0 0 18 16"><path d="M1 8h15M9 1l7 7-7 7" fill="none" stroke="#fff" stroke-width="2.4"/></svg></div>
  </section>

  <footer class="abs footer">
    <div class="col" style="left:89px"><h4>Halvard Peak Stores</h4><ul><li>Abbotsford</li><li>Canmore</li><li>Courtenay</li><li>Medicine Hat</li><li>Nanaimo</li><li>Nelson</li><li>New Denver</li></ul></div>
    <div class="col" style="left:290px"><h4>Quick Links</h4><ul><li>Resucue Gear</li><li>Footwear</li><li>Clothing</li><li>Tents, Mats, Sleeping Bags</li><li>Camping Gear</li><li>Snow Sports</li><li>Brands</li></ul></div>
    <div class="col" style="left:457px"><h4>Products For</h4><ul><li>Search &amp; Rescue</li><li>Coast Guard</li><li>NVDK</li><li>Fire</li><li>Military</li><li>Law Enforcement</li></ul></div>
    <div class="col" style="left:612px"><h4>Newsletter</h4><p>Don’t miss anynews. Subscribe to our Newsletter!</p><div class="input">Name....</div><div class="input">Mail....</div><span class="sub">Subscribe</span></div>
  </footer>
  <div class="abs bottom"></div>
  <div class="abs copy">© 2014 Halvard Peak Outfitters Inc. All rights reserved.</div>
  <div class="abs social"><i></i><i></i><i></i><i></i></div>

</div>
</body>
</html>
```